Breakfast Cafe - The Sunny Nook

It is for my breakfast and lunch cafe with a hawaiian / beach theme. I am open 7 days a week from 7am to 2pm. We serve traditional American food such as omelettes, pancakes, burgers and sandwiches. I'll upload my old card and my new logo to be used. We have a lot of day to day regulars who eat there during the week, our t-shirts actually say 'Locals Only' on them. Hope this helps. Thanks.

Target Market(s)

anyone who has an appetite!

Industry/Entity Type

American Restaurant

Contact Information for Business Card

4815C Marlow Grove Avenue
Long Beach, California
(555) 731-2294

Requirements
Must have
• Address and phone number easily readable.
Nice to have
• beach or tropical theme

```html
<!DOCTYPE html>
<html lang="en">
<head>
<meta charset="utf-8">
<title>The Sunny Nook – Business Card</title>
<link rel="stylesheet" href="https://fonts.googleapis.com/css2?family=Lato:wght@400;900&display=swap">
<style>
  :root {
    --backdrop: #e6e6e6;
    --ink: #141414;
    --sky: #1e6fe0;
    --sea-deep: #1aa0d8;
    --sea-light: #3fd2e0;
    --sand: #e8ddc8;
    --foliage: #2f7d2a;
    --card-blue: #5bbfd6;
    --accent-orange: #b8621f;
    --badge: #e9a34a;
    --name-white: #ffffff;
    --shadow: rgba(0, 0, 0, 0.35);
  }
  * { box-sizing: border-box; margin: 0; padding: 0; }
  html, body { width: 1000px; height: 1200px; overflow: hidden; }
  body {
    position: relative;
    background: var(--backdrop);
    font-family: "Lato", sans-serif;
    color: var(--ink);
  }
  .card {
    position: absolute;
    left: 214px;
    width: 578px;
    height: 357px;
    overflow: hidden;
    box-shadow: 3px 4px 6px var(--shadow);
  }
  .card--front { top: 219px; border-radius: 0 48px 0 48px; }
  .card--back  { top: 607px; border-radius: 48px 0 48px 0; background: var(--card-blue); }

  .beach-scene {
    position: absolute; inset: 0;
    background: linear-gradient(180deg,
      var(--sky) 0%, var(--sky) 14%,
      var(--sea-deep) 17%, var(--sea-light) 62%,
      var(--sand) 70%, var(--sand) 82%,
      var(--foliage) 90%, var(--foliage) 100%);
  }
  .front-content { position: absolute; inset: 0; }
  .brand-name {
    position: absolute; left: 62px; top: 28px;
    font-size: 46px; font-weight: 900; color: var(--name-white);
    letter-spacing: 1px; white-space: nowrap;
  }
  .tagline { position: absolute; left: 56px; top: 94px; font-size: 27px; white-space: nowrap; }
  .phone {
    position: absolute; left: 56px; top: 141px; font-size: 21px;
    display: flex; align-items: center; gap: 6px; white-space: nowrap;
  }
  .address { position: absolute; left: 55px; top: 171px; font-size: 21px; line-height: 27px; white-space: nowrap; }
  .hours { position: absolute; left: 56px; top: 248px; font-size: 25px; white-space: nowrap; }

  .badge-circle {
    position: absolute; left: 209px; top: 30px;
    width: 160px; height: 160px; border-radius: 50%;
    background: var(--badge);
  }
  .back-name {
    position: absolute; left: 0; right: 0; top: 200px;
    text-align: center; font-size: 38px; font-weight: 900; color: var(--badge);
    line-height: 46px; white-space: nowrap;
  }
  .back-locale {
    position: absolute; left: 0; right: 0; top: 254px;
    text-align: center; font-size: 12px; font-weight: 900; letter-spacing: 3px;
    color: var(--accent-orange);
  }
  .menu-line {
    position: absolute; left: 0; right: 0; top: 293px;
    text-align: center; font-size: 21.5px; color: var(--accent-orange); white-space: nowrap;
  }
</style>
</head>
<body>
  <section class="card card--front">
    <div class="beach-scene" role="img" aria-label="Tropical beach photo: turquoise sea with two islands, sandy shore and green shrubs"></div>
    <div class="front-content">
      <div class="brand-name">The Sunny Nook</div>
      <p class="tagline">Family owned and operated!</p>
      <p class="phone">
        <svg width="22" height="22" viewBox="0 0 22 22" aria-hidden="true">
          <rect width="22" height="22" rx="3" fill="#141414"/>
          <path d="M7 5c1 0 2 2 2 3s-1 1-1 2 2 3 3 3 1-1 2-1 3 1 3 2-1 2-2 2C9 16 6 10 6 7c0-1 0-2 1-2z" fill="#fff"/>
        </svg>
        (555) 731-2294
      </p>
      <p class="address">4815C Marlow Grove Avenue<br>Long Beach, California</p>
      <p class="hours">Breakfast &amp; Lunch 7am - 2pm Daily</p>
    </div>
  </section>

  <section class="card card--back">
    <div class="badge-circle"></div>
    <div class="back-name">The Sunny Nook</div>
    <p class="back-locale">LONG BEACH, CA</p>
    <p class="menu-line">Omelettes | Pancakes | Burgers | Sandwiches</p>
  </section>
</body>
</html>
```